Box Design for Flooring product

***IMPORTANT: PLEASE READ THE DOCUMENT PROVIDED WITH THIS BRIEF CAREFULLY BEFORE ACCEPTING THIS PROJECT***
Need a creative design for the packaging of a flooring product. The packaging is two boxes: one holding 36 planks of flooring, and the other 7 planks of flooring. There are 4 colours for the flooring planks that need a box designed (for both the 36 plank box and 7 plank box). The boxes measures 92 cm x 16cm x 7cm (36 planks) and 92 cm x 16cm x 1.5cm (7 planks).
More details are provided in the requirements document attached with this brief. Also attaching other supporting documents with this brief mentioned in the document.
Updates
Font styles to use
Other font styles liked:
- Montserrat-Regular
Look and feel
Each slider illustrates characteristics of the customer's brand and the style your logo design should communicate.

```html
<!DOCTYPE html>
<html lang="en">
<head>
<meta charset="utf-8">
<title>Flooring Box – 7 Plank Pack</title>
<link href="https://fonts.googleapis.com/css2?family=Montserrat:ital,wght@0,400;0,500;0,700;0,800;1,700;1,800&display=swap" rel="stylesheet">
<style>
  :root{
    --bg:#f3f3f3;
    --top-green:#37504d;
    --front-green:#334545;
    --paper:#f0f0f0;
    --ink:#2f3b3b;
    --wood-light:#e0ad5f;
    --wood-dark:#c98b3e;
    --room-wall:#a9acad;
    --room-floor:#d6a25a;
    --white:#ffffff;
  }
  *{box-sizing:border-box;margin:0;padding:0}
  html,body{width:1200px;height:750px;overflow:hidden;background:var(--bg);font-family:'Montserrat',sans-serif;color:var(--ink)}
  .canvas{position:relative;width:1200px;height:750px}

  /* top face */
  .top-face{position:absolute;left:50px;top:180px;width:1040px;height:220px;background:var(--paper);overflow:hidden}
  .top-face .brand{position:absolute;left:34px;top:34px;font-size:26px;font-weight:400;letter-spacing:4px;color:#4a4a46;display:flex;align-items:center;gap:10px}
  .brand-dot{width:14px;height:14px;background:currentColor}
  .room-photo{position:absolute;inset:0;clip-path:polygon(210px 100px,380px 100px,300px 220px,130px 220px);
    background:linear-gradient(180deg,var(--room-wall) 0 45%,var(--room-floor) 45% 100%)}
  .green-band{position:absolute;inset:0;background:var(--top-green);clip-path:polygon(380px 0,800px 0,720px 220px,300px 220px)}
  .wood{position:absolute;inset:0;clip-path:polygon(800px 0,960px 0,880px 220px,720px 220px);
    background:linear-gradient(100deg,var(--wood-light),var(--wood-dark) 55%,var(--wood-light))}
  .features{position:absolute;left:400px;top:34px;list-style:none;color:var(--white);font-weight:800;font-style:italic;font-size:17px;line-height:27px;white-space:nowrap}
  .features li{display:flex;align-items:center;gap:8px}
  .features svg{flex:none}
  .badge{position:absolute;left:700px;top:150px;width:190px;height:56px;background:var(--white);display:flex;align-items:center;gap:14px;padding:0 16px;box-shadow:0 2px 4px rgba(0,0,0,.15)}
  .badge-text{font-weight:800;font-size:17px;line-height:18px;color:#111}
  .spec-end{position:absolute;right:22px;top:38px;text-align:right;color:var(--ink)}
  .spec-end .label{font-weight:800;font-size:15px}
  .spec-end .value{font-size:13px;margin-bottom:8px}
  .spec-end .rule{height:2px;background:var(--ink);margin:4px 0 8px}

  /* front face */
  .front-face{position:absolute;left:50px;top:400px;width:1040px;height:130px;background:var(--front-green);color:var(--white)}
  .coverage{position:absolute;left:30px;top:36px}
  .coverage .label{font-weight:800;font-size:20px}
  .coverage .value{font-size:15px}
  .front-brand{position:absolute;left:50%;top:42px;transform:translateX(-50%);font-size:36px;font-weight:400;letter-spacing:6px;display:flex;align-items:center;gap:14px}
  .plank-size{position:absolute;right:30px;top:22px;text-align:right}
  .plank-size .label{font-weight:800;font-size:22px}
  .plank-size .value{font-size:22px;line-height:24px}
  .plank-size .approx{font-size:14px}

  /* end panel */
  .end-face{position:absolute;left:1090px;top:400px;width:60px;height:130px;background:var(--paper);border-left:1px solid #ddd}
  .cert{position:absolute;left:20px;top:14px;width:20px;height:20px;border:2px solid var(--ink);border-radius:50%}
  .end-brand{position:absolute;left:50%;bottom:44px;transform:translateX(-50%) rotate(-90deg);font-size:10px;letter-spacing:2px;color:var(--ink);white-space:nowrap}
</style>
</head>
<body>
<main class="canvas">
  <section class="top-face">
    <div class="green-band"></div>
    <div class="room-photo" role="img" aria-label="Room interior with warm oak plank floor, grey panelled wall and white side table"></div>
    <div class="wood" role="img" aria-label="Close-up of golden oak wood grain plank"></div>
    <div class="brand"><span class="brand-dot"></span>VERANTO</div>
    <ul class="features">
      <li><svg width="12" height="10" viewBox="0 0 12 10"><path d="M1 1l5 4-5 4M6 1l5 4-5 4" stroke="#fff" stroke-width="2" fill="none"/></svg>Easy to lay</li>
      <li><svg width="12" height="10" viewBox="0 0 12 10"><path d="M1 1l5 4-5 4M6 1l5 4-5 4" stroke="#fff" stroke-width="2" fill="none"/></svg>Easy to clean</li>
      <li><svg width="12" height="10" viewBox="0 0 12 10"><path d="M1 1l5 4-5 4M6 1l5 4-5 4" stroke="#fff" stroke-width="2" fill="none"/></svg>Ideal for Bathrooms and Kitchens</li>
      <li><svg width="12" height="10" viewBox="0 0 12 10"><path d="M1 1l5 4-5 4M6 1l5 4-5 4" stroke="#fff" stroke-width="2" fill="none"/></svg>Suitable for general domestic use</li>
    </ul>
    <div class="badge">
      <svg width="34" height="34" viewBox="0 0 34 34"><circle cx="17" cy="17" r="15" fill="none" stroke="#111" stroke-width="2.5"/><path d="M17 7c-4 6-6 9-6 12a6 6 0 0012 0c0-3-2-6-6-12z" fill="none" stroke="#111" stroke-width="2"/><path d="M13 19l3 3 5-6" fill="none" stroke="#111" stroke-width="2"/></svg>
      <div class="badge-text">Water<br>Resistant</div>
    </div>
    <div class="spec-end">
      <div class="label">Plank size</div>
      <div class="value">914mm x 152mm</div>
      <div class="rule"></div>
      <div class="label">Pack coverage 1m²</div>
      <div class="value">7 planks per pack</div>
    </div>
  </section>

  <section class="front-face">
    <div class="coverage">
      <div class="label">Pack coverage 1m²</div>
      <div class="value">7 planks per pack</div>
    </div>
    <div class="front-brand"><span class="brand-dot"></span>VERANTO</div>
    <div class="plank-size">
      <div class="label">Plank size</div>
      <div class="value">914mm x 152mm</div>
      <div class="approx">(36" x 6" approx.)</div>
    </div>
  </section>

  <section class="end-face">
    <div class="cert"></div>
    <div class="end-brand">VERANTO</div>
  </section>
</main>
</body>
</html>
```